Vorlanta PowerPoint Template

I have a company called Vorlanta, LLC and my company logo is already designed. I need a PowerPoint template that I will be using to pitch potential investors and business partners. This should be a very professional-looking template that leverages the company logo colors and really pops. The company is an AI product research and development company.

```html
<!DOCTYPE html>
<html lang="en">
<head>
<meta charset="utf-8">
<title>Vorlanta Presentation Template</title>
<link href="https://fonts.googleapis.com/css2?family=Archivo+Black&family=Montserrat:wght@400;500;600;700;800&display=swap" rel="stylesheet">
<style>
:root{
  --red:#b5121b;
  --ink:#3a3a3a;
  --dark:#3b3b3b;
  --grey:#e2e0e1;
  --stage:#5a5a5a;
  --white:#ffffff;
  --body:#4a4a4a;
}
*{margin:0;padding:0;box-sizing:border-box}
html,body{width:1011px;height:1200px;overflow:hidden;background:var(--stage)}
body{position:relative;font-family:"Montserrat",Arial,sans-serif;color:var(--ink)}
.slide{position:absolute;width:431px;height:242px;background:var(--white);overflow:hidden}
.abs{position:absolute}

/* header */
.brand{position:absolute;left:10px;top:12px;display:flex;align-items:center;gap:5px}
.brand .dot{width:20px;height:20px;border-radius:50%;background:var(--red)}
.brand .name{font-family:"Montserrat",Arial,sans-serif;font-weight:700;font-size:17px;color:var(--ink);letter-spacing:-.3px}
.divider{position:absolute;left:116px;top:12px;width:1px;height:23px;background:var(--ink)}
.slide-title{position:absolute;left:126px;top:17px;font-family:"Archivo Black",Arial,sans-serif;font-size:11px;color:var(--ink)}
.slide-title em{font-style:normal;color:var(--red)}

.para{font-size:4.6px;line-height:7.6px;color:var(--body);text-align:justify}
.para+.para{margin-top:7px}

/* cover */
.cover{background:radial-gradient(ellipse at center,#ffffff 40%,#eceef2 100%)}
.cover .net{position:absolute;left:0;width:431px;height:60px;background:linear-gradient(#dfe2e8,#f6f7f9)}
.cover .brand-lg{position:absolute;left:0;right:0;top:80px;display:flex;justify-content:center;align-items:center;gap:6px}
.brand-lg .dot{width:30px;height:30px;border-radius:50%;background:var(--red)}
.brand-lg .name{font-weight:700;font-size:26px;color:var(--ink);letter-spacing:-.5px}
.cover .tagline{position:absolute;left:0;right:0;top:121px;text-align:center;font-weight:800;font-size:15.5px;line-height:22px;color:var(--ink)}
.tagline .hl{color:var(--red)}

/* summary table */
.table{position:absolute;left:9px;top:45px;width:414px;height:187px;border:1px solid #e9a9ad}
.table .head{height:13px;display:flex}
.table .head div{flex:1;background:var(--red);color:var(--white);font-size:7.5px;padding:2px 5px;line-height:9px}
.table .head div+div{margin-left:2px}
.table .row{display:flex;height:57px}
.table .row.shade .cell{background:var(--grey)}
.cell{flex:1;padding:6px 10px}
.cell+.cell{margin-left:2px}
.cell h4{font-size:6.6px;font-weight:600;color:#222;margin-bottom:3px}
.cell li{list-style:none;font-size:4.6px;line-height:8.3px;color:#333;position:relative;padding-left:6px}
.cell li::before{content:"";position:absolute;left:0;top:2.6px;border-left:3px solid var(--red);border-top:1.6px solid transparent;border-bottom:1.6px solid transparent}

/* dark panel */
.panel{position:absolute;background:var(--dark);color:var(--white);padding:18px 13px 0 13px}
.panel h3{font-family:"Archivo Black",Arial,sans-serif;font-size:10.5px;line-height:12.5px;margin-bottom:14px}
.panel p{font-size:4.9px;line-height:7.6px;color:#e6e6e6}

.photo{position:absolute}

/* benefits */
.benefit{position:absolute;left:0;width:80px;text-align:center}
.benefit .ico{width:34px;height:34px;border-radius:50%;background:var(--red);margin:0 auto 5px;display:flex;align-items:center;justify-content:center}
.benefit span{font-family:"Archivo Black",Arial,sans-serif;font-size:5.8px;color:#222}

/* process */
.step{position:absolute;top:155px;width:84px;text-align:center}
.step h5{font-size:6.3px;font-weight:700;color:#222;margin-bottom:5px}
.step p{font-size:4.7px;line-height:6.4px;color:#333}

/* heading slide */
.col{position:absolute;top:46px;width:190px}
.bullets{margin-top:10px}
.bullets li{list-style:none;font-size:4.8px;line-height:10.8px;color:#333;position:relative;padding-left:8px}
.bullets li::before{content:"";position:absolute;left:0;top:3.3px;width:3.6px;height:3.6px;border-radius:50%;background:var(--red)}

/* thanks */
.thanks{background:linear-gradient(160deg,#1d1d1f,#0b0b0c 60%,#151516)}
.thanks .brand-lg{position:absolute;left:0;right:0;top:57px;display:flex;justify-content:center;align-items:center;gap:6px}
.thanks .brand-lg .name{color:#4a4a4a}
.thanks .rule{position:absolute;left:137px;width:172px;height:2px;background:var(--red)}
.thanks h2{position:absolute;left:0;right:0;top:131px;text-align:center;font-family:"Archivo Black",Arial,sans-serif;font-size:27px;color:var(--white);letter-spacing:.5px}
</style>
</head>
<body>

<!-- Cover -->
<section class="slide cover" style="left:46px;top:54px">
  <div class="net" style="top:0" role="img" aria-label="Connected network dots pattern"></div>
  <div class="net" style="bottom:0;transform:scaleY(-1)" role="img" aria-label="Connected network dots pattern"></div>
  <div class="brand-lg"><div class="dot"></div><div class="name">Vorlanta</div></div>
  <div class="tagline"><span class="hl">AI PRODUCT RESEARCH</span> AND<br>DEVELOPMENT COMPANY.</div>
</section>

<!-- Report content summary -->
<section class="slide" style="left:509px;top:57px">
  <div class="brand"><div class="dot"></div><div class="name">Vorlanta</div></div>
  <div class="divider"></div>
  <div class="slide-title">Report <em>Content Summary</em></div>
  <div class="table">
    <div class="head"><div>Lorem Ipsum</div><div></div></div>
    <div class="row shade">
      <div class="cell"><h4>Lorem Ipsum is simply dummy text</h4><ul><li>Lorem ipsum dolor sit amet, consectetur adipisci</li><li>Sed ut perspiciatis unde omnis iste natus error sit volu</li><li>But I must explain to you how all this mistaken i</li><li>At vero eos et accusamus et iusto odio dignissimos duci</li></ul></div>
      <div class="cell"><h4>Lorem Ipsum is simply dummy text</h4><ul><li>Lorem ipsum dolor sit amet, consectetur adipisci</li><li>Sed ut perspiciatis unde omnis iste natus error sit volu</li><li>But I must explain to you how all this mistaken i</li><li>At vero eos et accusamus et iusto odio dignissimos duci</li></ul></div>
    </div>
    <div class="row">
      <div class="cell"><h4>Lorem Ipsum is simply dummy text</h4><ul><li>Lorem ipsum dolor sit amet, consectetur adipisci</li><li>Sed ut perspiciatis unde omnis iste natus error sit volu</li><li>But I must explain to you how all this mistaken i</li><li>At vero eos et accusamus et iusto odio dignissimos duci</li></ul></div>
      <div class="cell"><h4>Lorem Ipsum is simply dummy text</h4><ul><li>Lorem ipsum dolor sit amet, consectetur adipisci</li><li>Sed ut perspiciatis unde omnis iste natus error sit volu</li><li>But I must explain to you how all this mistaken i</li><li>At vero eos et accusamus et iusto odio dignissimos duci</li></ul></div>
    </div>
    <div class="row shade">
      <div class="cell"><h4>Lorem Ipsum is simply dummy text</h4><ul><li>Lorem ipsum dolor sit amet, consectetur adipisci</li><li>Sed ut perspiciatis unde omnis iste natus error sit volu</li><li>But I must explain to you how all this mistaken i</li><li>At vero eos et accusamus et iusto odio dignissimos duci</li></ul></div>
      <div class="cell"><h4>Lorem Ipsum is simply dummy text</h4><ul><li>Lorem ipsum dolor sit amet, consectetur adipisci</li><li>Sed ut perspiciatis unde omnis iste natus error sit volu</li><li>But I must explain to you how all this mistaken i</li><li>At vero eos et accusamus et iusto odio dignissimos duci</li></ul></div>
    </div>
  </div>
</section>

<!-- About us -->
<section class="slide" style="left:49px;top:327px">
  <div class="brand"><div class="dot"></div><div class="name">Vorlanta</div></div>
  <div class="divider"></div>
  <div class="slide-title">About <em>Us</em></div>
  <div class="abs" style="left:12px;top:44px;width:180px">
    <p class="para">Sed ut perspiciatis unde omnis iste natus error sit voluptatem accusantium doloremque laudantium, totam rem aperiam, eaque ipsa quae ab illo inventore veritatis et quasi architecto beatae vitae dicta sunt explicabo. Nemo enim ipsam voluptatem quia voluptas sit aspernatur aut odit aut fugit, sed quia consequuntur magni dolores eos qui ratione voluptatem sequi nesciunt. Neque porro quisquam est, qui dolorem ipsum quia dolor sit amet, consectetur, adipisci velit, sed quia non numquam eius modi tempora incidunt ut labore et dolore magnam aliquam quaerat voluptatem.</p>
    <p class="para">Sed ut perspiciatis unde omnis iste natus error sit voluptatem accusantium doloremque laudantium, totam rem aperiam, eaque ipsa quae ab illo inventore veritatis et quasi architecto beatae vitae dicta sunt explicabo. Nemo enim ipsam voluptatem quia voluptas sit aspernatur aut odit aut fugit, sed quia consequuntur magni dolores eos qui ratione voluptatem sequi nesciunt. Neque porro quisquam est, qui dolorem ipsum quia dolor sit amet, consectetur, adipisci velit, sed quia non numquam eius modi tempora incidunt ut labore et dolore magnam aliquam quaerat voluptatem.</p>
    <p class="para">Sed ut perspiciatis unde omnis iste natus error sit voluptatem accusantium doloremque laudantium, totam rem aperiam, eaque ipsa quae ab illo inventore veritatis et quasi architecto.</p>
  </div>
  <div class="photo" style="left:212px;top:0;width:219px;height:242px;background:linear-gradient(150deg,#1c2433,#233a63 45%,#0f1522)" role="img" aria-label="Person working on a laptop with floating holographic data charts"></div>
</section>

<!-- Profit -->
<section class="slide" style="left:509px;top:335px">
  <div class="brand"><div class="dot"></div><div class="name">Vorlanta</div></div>
  <div class="divider"></div>
  <div class="slide-title">Profit</div>
  <svg class="abs" style="left:0;top:0" width="300" height="242" viewBox="0 0 300 242" font-family="Montserrat, Arial, sans-serif" font-size="6" fill="#333">
    <g stroke="#333" stroke-width="0.5">
      <line x1="30" y1="173" x2="274" y2="173"/><line x1="30" y1="151" x2="274" y2="151"/>
      <line x1="30" y1="130" x2="274" y2="130"/><line x1="30" y1="108" x2="274" y2="108"/>
      <line x1="30" y1="87" x2="274" y2="87"/>
    </g>
    <g stroke="#333" stroke-width="0.5">
      <line x1="52" y1="194" x2="52" y2="183"/><line x1="74" y1="194" x2="74" y2="155"/>
      <line x1="97" y1="194" x2="97" y2="136"/><line x1="119" y1="194" x2="119" y2="134"/>
      <line x1="141" y1="194" x2="141" y2="115"/><line x1="163" y1="194" x2="163" y2="126"/>
      <line x1="185" y1="194" x2="185" y2="104"/><line x1="208" y1="194" x2="208" y2="128"/>
      <line x1="230" y1="194" x2="230" y2="106"/><line x1="252" y1="194" x2="252" y2="91"/>
    </g>
    <line x1="30" y1="60" x2="30" y2="194" stroke="#333" stroke-width="1"/>
    <line x1="30" y1="194" x2="274" y2="194" stroke="#333" stroke-width="1.5"/>
    <polyline fill="none" stroke="#8a2a15" stroke-width="1" points="30,194 52,183 74,155 97,136 119,134 141,115 163,126 185,104 208,128 230,106 252,91"/>
    <g text-anchor="end"><text x="22" y="89">100</text><text x="22" y="110">80</text><text x="22" y="132">60</text><text x="22" y="153">40</text><text x="22" y="175">20</text></g>
    <g text-anchor="middle"><text x="21" y="206">0</text><text x="52" y="206">10</text><text x="74" y="206">20</text><text x="97" y="206">30</text><text x="119" y="206">40</text><text x="141" y="206">50</text><text x="163" y="206">60</text><text x="185" y="206">70</text><text x="208" y="206">80</text><text x="230" y="206">90</text><text x="252" y="206">100</text></g>
  </svg>
  <div class="panel" style="left:300px;top:36px;width:131px;height:206px">
    <h3>Lorem ipsum dolor sit amet, consectetur</h3>
    <p>Sed ut perspiciatis unde omnis iste natus error sit voluptatem accusantium doloremque laudantium, totam rem aperiam, eaque ipsa quae ab illo inventore veritatis et quasi architecto beatae vitae dicta sunt explicabo. Nemo enim ipsam voluptatem quia voluptas sit aspernatur aut odit aut fugit, sed quia consequuntur magni dolores eos qui ratione voluptatem sequi nesciunt. Neque porro quisquam est, qui dolorem ipsum quia dolor sit amet, consectetur, adipisci velit, sed quia non numquam eius modi tempora incidunt ut labore et dolore magnam aliquam quaerat voluptatem. Ut enim ad minima veniam, quis nostrum exercitationem ullam corporis suscipit laboriosam, nisi ut aliquid</p>
  </div>
</section>

<!-- Benefits -->
<section class="slide" style="left:54px;top:610px">
  <div class="brand"><div class="dot"></div><div class="name">Vorlanta</div></div>
  <div class="divider"></div>
  <div class="slide-title">Benefits</div>
  <div class="benefit" style="top:48px"><div class="ico"><svg width="14" height="14" viewBox="0 0 14 14" fill="#fff"><path d="M7 1 1 4h12z"/><rect x="2" y="5" width="2" height="6"/><rect x="6" y="5" width="2" height="6"/><rect x="10" y="5" width="2" height="6"/><rect x="1" y="11.5" width="12" height="1.5"/></svg></div><span>Lorem ipsum</span></div>
  <div class="benefit" style="top:110px"><div class="ico"><svg width="16" height="14" viewBox="0 0 16 14" fill="#fff"><ellipse cx="9" cy="8" rx="6" ry="4.5"/><circle cx="5" cy="4" r="3.5"/></svg></div><span>Lorem ipsum</span></div>
  <div class="benefit" style="top:178px"><div class="ico"><svg width="14" height="14" viewBox="0 0 14 14" fill="#fff"><rect x="2" y="1" width="8" height="11" rx="1.5"/><path d="M8 12 13 6l1 1-5 6z"/></svg></div><span>Lorem ipsum</span></div>
  <div class="panel" style="left:80px;top:34px;width:132px;height:208px">
    <h3>Lorem ipsum dolor sit amet, consectetur</h3>
    <p>Sed ut perspiciatis unde omnis iste natus error sit voluptatem accusantium doloremque laudantium, totam rem aperiam, eaque ipsa quae ab illo inventore veritatis et quasi architecto beatae vitae dicta sunt explicabo. Nemo enim ipsam voluptatem quia voluptas sit aspernatur aut odit aut fugit, sed quia consequuntur magni dolores eos qui ratione voluptatem sequi nesciunt. Neque porro quisquam est, qui dolorem ipsum quia dolor sit amet, consectetur, adipisci velit, sed quia non numquam eius modi tempora incidunt ut labore et dolore magnam aliquam quaerat voluptatem. Ut enim ad minima veniam, quis nostrum exercitationem ullam corporis suscipit laboriosam, nisi ut aliquid</p>
  </div>
  <div class="photo" style="left:212px;top:34px;width:219px;height:208px;background:radial-gradient(ellipse at 65% 40%,#2f8a5a,#0d3326 55%,#061712)" role="img" aria-label="Glowing green upward arrow over a dark financial chart"></div>
</section>

<!-- Our process -->
<section class="slide" style="left:512px;top:613px">
  <div class="brand"><div class="dot"></div><div class="name">Vorlanta</div></div>
  <div class="divider"></div>
  <div class="slide-title">Our <em>Process</em></div>
  <svg class="abs" style="left:0;top:0" width="431" height="150" viewBox="0 0 431 150">
    <g fill="none" stroke="#b5121b" stroke-width="0.8" stroke-dasharray="3 2">
      <circle cx="68" cy="99" r="50"/><circle cx="164" cy="99" r="50"/><circle cx="265" cy="99" r="50"/><circle cx="365" cy="99" r="50"/>
    </g>
    <path d="M72 48 l-4 -2.5 v5z" fill="#b5121b" transform="translate(4,0)"/>
    <path d="M361 150 l4 -2.5 v5z" fill="#b5121b" transform="translate(-6,-1)"/>
    <g fill="#b5121b"><circle cx="68" cy="99" r="37"/><circle cx="164" cy="99" r="37"/><circle cx="265" cy="99" r="37"/><circle cx="365" cy="99" r="37"/></g>
    <g fill="none" stroke="#fff" stroke-width="1.2">
      <rect x="56" y="86" width="22" height="28" rx="1.5"/><line x1="60" y1="92" x2="74" y2="92"/><circle cx="60" cy="103" r="3"/><polyline points="66,110 66,104 70,106 70,110 74,110 74,100"/>
      <circle cx="164" cy="99" r="12"/><circle cx="164" cy="99" r="7"/><polyline points="160,102 163,98 166,100 169,95"/>
      <rect x="251" y="87" width="28" height="18" rx="1"/><line x1="251" y1="91" x2="279" y2="91"/><line x1="255" y1="95" x2="270" y2="95"/><path d="M258 104 l8 -4 v12 l-8 -4z"/>
      <rect x="350" y="89" width="20" height="14"/><polyline points="353,100 357,95 361,97 368,90"/><circle cx="372" cy="106" r="6"/><circle cx="372" cy="106" r="2.5"/>
    </g>
  </svg>
  <div class="step" style="left:26px"><h5>LOREM IPSUM</h5><p>Lorem ipsum dolor sit amet, consectetur adipiscing elit, sed do eiusmod tempor incididunt ut labore et dolore magna aliqua. Ut enim ad minim veniam, quis nostrud exerci tation xcepteur sint occaecat cupidatat non pro.</p></div>
  <div class="step" style="left:122px"><h5>LOREM IPSUM</h5><p>Lorem ipsum dolor sit amet, consectetur adipiscing elit, sed do eiusmod tempor incididunt ut labore et dolore magna aliqua. Ut enim ad minim veniam, quis nostrud exerci tation xcepteur sint occaecat cupidatat non pro.</p></div>
  <div class="step" style="left:223px"><h5>LOREM IPSUM</h5><p>Lorem ipsum dolor sit amet, consectetur adipiscing elit, sed do eiusmod tempor incididunt ut labore et dolore magna aliqua. Ut enim ad minim veniam, quis nostrud exerci tation xcepteur sint occaecat cupidatat non pro.</p></div>
  <div class="step" style="left:323px"><h5>LOREM IPSUM</h5><p>Lorem ipsum dolor sit amet, consectetur adipiscing elit, sed do eiusmod tempor incididunt ut labore et dolore magna aliqua. Ut enim ad minim veniam, quis nostrud exerci tation xcepteur sint occaecat cupidatat non pro.</p></div>
</section>

<!-- Heading -->
<section class="slide" style="left:60px;top:890px">
  <div class="brand"><div class="dot"></div><div class="name">Vorlanta</div></div>
  <div class="divider"></div>
  <div class="slide-title">Heading</div>
  <div class="abs" style="left:217px;top:46px;width:1px;height:196px;background:#e4e4e4"></div>
  <div class="col" style="left:16px">
    <p class="para">Sed ut perspiciatis unde omnis iste natus error sit voluptatem accusantium doloremque laudantium, totam rem aperiam, eaque ipsa quae ab illo inventore veritatis et quasi architecto beatae vitae dicta sunt explicabo. Nemo enim ipsam voluptatem quia voluptas sit aspernatur aut odit aut fugit, sed quia consequuntur magni dolores eos qui ratione voluptatem sequi nesciunt. Neque porro quisquam est, qui dolorem ipsum quia dolor sit amet, consectetur, adipisci velit, sed quia non numquam eius modi tempora incidunt ut labore et dolore magnam aliquam quaerat voluptatem. Ut enim ad minima veniam, quis nostrum exercitationem ullam corporis suscipit laboriosam, nisi ut aliquid</p>
    <ul class="bullets"><li>Lorem ipsum dolor sit amet, consectetur adipiscing elit.</li><li>Duis at velit in magna consectetur sollicitudin ut et lacus.</li><li>Praesent molestie arcu eget semper commodo.</li><li>Sed elementum leo et dolor varius, sit amet vestibulum tortor volutpat.</li><li>Praesent varius ante at ipsum consectetur sodales sed eu nibh.</li><li>Sed malesuada mi eget est maximus mattis.</li><li>Nam nec dolor sagittis, pellentesque lectus a, consectetur purus.</li><li>Praesent a augue in diam suscipit tincidunt ut nec velit.</li></ul>
  </div>
  <div class="col" style="left:230px">
    <p class="para">Sed ut perspiciatis unde omnis iste natus error sit voluptatem accusantium doloremque laudantium, totam rem aperiam, eaque ipsa quae ab illo inventore veritatis et quasi architecto beatae vitae dicta sunt explicabo. Nemo enim ipsam voluptatem quia voluptas sit aspernatur aut odit aut fugit, sed quia consequuntur magni dolores eos qui ratione voluptatem sequi nesciunt. Neque porro quisquam est, qui dolorem ipsum quia dolor sit amet, consectetur, adipisci velit, sed quia non numquam eius modi tempora incidunt ut labore et dolore magnam aliquam quaerat voluptatem. Ut enim ad minima veniam, quis nostrum exercitationem ullam corporis suscipit laboriosam, nisi ut aliquid</p>
    <ul class="bullets"><li>Lorem ipsum dolor sit amet, consectetur adipiscing elit.</li><li>Duis at velit in magna consectetur sollicitudin ut et lacus.</li><li>Praesent molestie arcu eget semper commodo.</li><li>Sed elementum leo et dolor varius, sit amet vestibulum tortor volutpat.</li><li>Praesent varius ante at ipsum consectetur sodales sed eu nibh.</li><li>Sed malesuada mi eget est maximus mattis.</li><li>Nam nec dolor sagittis, pellentesque lectus a, consectetur purus.</li><li>Praesent a augue in diam suscipit tincidunt ut nec velit.</li></ul>
  </div>
</section>

<!-- Thank you -->
<section class="slide thanks" style="left:517px;top:893px" role="img" aria-label="Dark dimmed office scene background">
  <div class="brand-lg"><div class="dot"></div><div class="name">Vorlanta</div></div>
  <div class="rule" style="top:124px"></div>
  <h2>THANK YOU</h2>
  <div class="rule" style="top:169px"></div>
</section>

</body>
</html>
```